Jewelers Website

This is for the DESIGN ONLY.
I am a software programmer and will be doing the development.
New website design for
www.lunacrestgems.com.au
Need a fresh new look for an online only jewellery business who produce their jewellery by hand. I would like it designed in a parallax style. Feel free to recommend fonts to use for the site. This is an Australian based company located in NSW so shots of sites in NSW might make nice background images.
http://vornaplex.me/demo/#theme=parallax
To contain the below sections
About Us
Contact Us
Gallery
Testimonials
Diamond Types
The colour scheme is to be Black / White and Silver.
With the Parallax style there will be moving sections and images for added impact.
Target Market(s)
Young Adults mainly engagement jewellery

```html
<!DOCTYPE html>
<html lang="en">
<head>
<meta charset="utf-8">
<title>Lunacrest Gems — Handmade Jewellery</title>
<link rel="stylesheet" href="https://fonts.googleapis.com/css2?family=Roboto:wght@300;400;500&display=swap">
<style>
  :root{
    --black:#000;
    --ink:#0b0b0b;
    --nav:#141414;
    --nav-active:#222;
    --panel:#2b2b2b;
    --band:#111;
    --footer:#0f0f0f;
    --white:#fff;
    --silver:#c9c9c9;
    --muted:#8a8a8a;
    --dim:#5e5e5e;
    --line:#9a9a9a;
  }
  *{margin:0;padding:0;box-sizing:border-box}
  html,body{width:1200px;height:2769px;overflow:hidden;background:var(--black)}
  body{position:relative;font-family:'Roboto',Arial,sans-serif;color:var(--white)}
  .abs{position:absolute}
  .upper{text-transform:uppercase}

  /* hero */
  .hero{left:0;top:0;width:1200px;height:519px;background:var(--black)}
  .hero-photo{left:554px;top:0;width:646px;height:519px;
    background:radial-gradient(ellipse at 55% 35%,#8a8a8a 0%,#3c3c3c 28%,#111 60%,#000 80%)}
  .brand{left:166px;top:120px;font-size:24px;font-weight:400;letter-spacing:1px;line-height:26px;color:var(--silver)}
  .hero-title{left:164px;top:210px;font-size:30px;font-weight:400;letter-spacing:.5px}
  .hero-text{left:164px;top:264px;width:330px;font-size:10.5px;line-height:20px;color:var(--silver)}
  .btn-outline{border:1.5px solid var(--line);color:var(--white);display:flex;align-items:center;justify-content:center;font-size:10px;letter-spacing:.4px}
  .hero-btn{left:162px;top:351px;width:216px;height:44px}
  .arrow{width:24px;height:80px}

  /* nav */
  .main-nav{left:0;top:519px;width:1200px;height:59px;background:var(--nav)}
  .nav-item{top:0;height:59px;line-height:59px;font-size:10.5px;color:var(--silver)}
  .nav-active{left:170px;width:122px;background:var(--nav-active);text-align:center;color:var(--white)}

  /* welcome */
  .welcome{left:0;top:578px;width:1200px;height:222px;background:var(--black);text-align:center}
  .section-title{font-size:21px;font-weight:400;letter-spacing:.5px}
  .welcome .section-title{position:absolute;top:58px;width:100%}
  .welcome-text{position:absolute;left:260px;top:108px;width:680px;font-size:10px;line-height:23px;color:var(--muted)}

  /* about */
  .about-photo{left:0;top:800px;width:605px;height:415px;
    background:linear-gradient(110deg,#1a1a1a 0%,#6a5a50 35%,#a08c80 50%,#3a3a3a 75%,#222 100%)}
  .about-panel{left:605px;top:800px;width:595px;height:415px;background:var(--panel)}
  .about-kicker{left:84px;top:52px;font-size:21px}
  .about-title{left:84px;top:82px;font-size:26px;color:var(--silver);font-weight:300}
  .about-text{left:84px;top:128px;width:330px;font-size:9px;line-height:22px;color:var(--muted)}
  .about-btn{left:84px;top:332px;width:129px;height:34px;font-size:10px}

  /* gallery */
  .gallery{left:0;top:1215px;width:1200px;height:718px;
    background:radial-gradient(ellipse at 50% 40%,#2a2a2a 0%,#111 55%,#060606 100%)}
  .gallery .section-title{position:absolute;top:62px;width:100%;text-align:center}
  .tile{width:255px;height:244px;background:linear-gradient(135deg,#555 0%,#3a3a3a 60%,#2e2e2e 100%)}
  .tile-label{position:absolute;left:28px;top:88px;width:198px;height:81px;border:2px solid #b5b5b5;
    display:flex;flex-direction:column;align-items:center;justify-content:center;font-size:16px;line-height:26px}

  /* testimonials */
  .testimonials{left:0;top:1933px;width:1200px;height:290px;background:var(--band)}
  .testimonials .section-title{position:absolute;top:58px;width:100%;text-align:center}
  .avatar{width:110px;height:110px;border-radius:50%;background:radial-gradient(circle at 45% 40%,#8c7566,#3a2d26 70%)}
  .quote-name{font-size:12px;letter-spacing:.3px}
  .quote-date{font-size:9.5px;font-style:italic;color:var(--dim)}
  .quote-text{width:290px;font-size:11px;line-height:22px;color:var(--dim)}

  /* diamond types */
  .types{left:0;top:2223px;width:1200px;height:450px;
    background:radial-gradient(ellipse at 50% 20%,#3a3a3a 0%,#1c1c1c 50%,#0c0c0c 100%)}
  .types .section-title{position:absolute;top:64px;width:100%;text-align:center}
  .types-text{position:absolute;left:220px;top:104px;width:760px;text-align:center;font-size:10px;line-height:23px;color:var(--white)}
  .type-card{width:197px;top:171px}
  .type-photo{width:197px;height:172px}
  .type-name{margin-top:20px;text-align:center;font-size:10.5px;font-weight:500}
  .type-link{margin-top:8px;text-align:center;font-size:8px}

  /* footer */
  .site-footer{left:0;top:2673px;width:1200px;height:96px;background:var(--footer)}
  .foot-link{top:34px;font-size:8.5px;color:var(--muted)}
  .copyright{left:175px;top:60px;font-size:8.5px;color:var(--muted)}
  .social{top:35px;width:26px;height:26px;border-radius:50%;background:#4a4a4a}
</style>
</head>
<body>

<header class="hero abs">
  <div class="hero-photo abs" role="img" aria-label="Cut diamonds on a black reflective surface"></div>
  <div class="brand abs upper">Lunacrest<br>Gems</div>
  <h1 class="hero-title abs upper">Lunacrest Gems</h1>
  <p class="hero-text abs upper">At Lunacrest Gems we are passionate about fine jewellery and gems. We feature one of a kind, original and elegant, handmade pieces...</p>
  <a class="hero-btn btn-outline abs upper">Click here for more details</a>
  <svg class="arrow abs" style="left:80px;top:196px" viewBox="0 0 24 80"><polyline points="20,4 4,40 20,76" fill="none" stroke="#444" stroke-width="2"/></svg>
  <svg class="arrow abs" style="left:1118px;top:196px" viewBox="0 0 24 80"><polyline points="4,4 20,40 4,76" fill="none" stroke="#444" stroke-width="2"/></svg>
</header>

<nav class="main-nav abs">
  <span class="nav-item nav-active abs upper">Home</span>
  <span class="nav-item abs upper" style="left:330px">About Us</span>
  <span class="nav-item abs upper" style="left:466px">Contact Us</span>
  <span class="nav-item abs upper" style="left:612px">Gallery</span>
  <span class="nav-item abs upper" style="left:741px">Testimonials</span>
  <span class="nav-item abs upper" style="left:898px">Diamond Types</span>
</nav>

<section class="welcome abs">
  <h2 class="section-title upper">Welcome to Lunacrest Gems</h2>
  <p class="welcome-text upper">At Lunacrest Gems we are passionate about fine jewellery and gems. We feature one of a kind, original and elegant, handmade pieces. Lunacrest Gems handmade jewellery is crafted using exceptional quality metals, integrating designs that are innovative, creative, and unique.</p>
</section>

<section class="about">
  <div class="about-photo abs" role="img" aria-label="Model wearing jewellery and dark glasses"></div>
  <div class="about-panel abs">
    <h2 class="about-kicker abs upper">About</h2>
    <div class="about-title abs upper">Lunacrest Gems</div>
    <div class="about-text abs upper">
      <p>At Lunacrest Gems we are passionate about fine jewellery and gems. We feature one of a kind, original and elegant, handmade pieces. Lunacrest Gems handmade jewellery is crafted using exceptional quality metals, integrating designs that are innovative, creative, and unique.</p>
      <p style="margin-top:22px">After you have consulted with our experienced staff - our highly trained and experienced jewellers hand-make every piece of finely crafted jewellery with a level of care...</p>
    </div>
    <a class="about-btn btn-outline abs upper">About more &nbsp;»</a>
  </div>
</section>

<section class="gallery abs">
  <h2 class="section-title upper">Gallery</h2>
  <div class="tile abs" style="left:172px;top:121px" role="img" aria-label="Loose diamonds"><div class="tile-label upper"><span>Diamond Grading</span><span>View Large</span></div></div>
  <div class="tile abs" style="left:463px;top:121px" role="img" aria-label="Diamond close-up"><div class="tile-label upper"><span>Diamond Grading</span><span>View Large</span></div></div>
  <div class="tile abs" style="left:755px;top:121px" role="img" aria-label="Scattered gemstones"><div class="tile-label upper"><span>Diamond Grading</span><span>View Large</span></div></div>
  <div class="tile abs" style="left:172px;top:395px" role="img" aria-label="Diamond necklace"><div class="tile-label upper"><span>Diamond Grading</span><span>View Large</span></div></div>
  <div class="tile abs" style="left:463px;top:395px" role="img" aria-label="Single cut diamond"><div class="tile-label upper"><span>Diamond Grading</span><span>View Large</span></div></div>
  <div class="tile abs" style="left:755px;top:395px" role="img" aria-label="Pile of diamonds"><div class="tile-label upper"><span>Diamond Grading</span><span>View Large</span></div></div>
</section>

<section class="testimonials abs">
  <h2 class="section-title upper">Testimonials</h2>
  <svg class="abs" style="left:132px;top:150px" width="12" height="36" viewBox="0 0 12 36"><polyline points="10,2 2,18 10,34" fill="none" stroke="#333" stroke-width="1.5"/></svg>
  <svg class="abs" style="left:1042px;top:150px" width="12" height="36" viewBox="0 0 12 36"><polyline points="2,2 10,18 2,34" fill="none" stroke="#333" stroke-width="1.5"/></svg>

  <div class="avatar abs" style="left:200px;top:113px" role="img" aria-label="Customer portrait"></div>
  <div class="quote-name abs upper" style="left:338px;top:128px">Talia Verens</div>
  <div class="quote-date abs" style="left:338px;top:150px">Posted on 27 march 2014</div>
  <p class="quote-text abs" style="left:338px;top:168px">It is a long established fact that a reader will be distracted by the readable content...</p>

  <div class="avatar abs" style="left:637px;top:113px" role="img" aria-label="Customer portrait"></div>
  <div class="quote-name abs upper" style="left:775px;top:128px">Talia Verens</div>
  <div class="quote-date abs" style="left:775px;top:150px">Posted on 27 march 2014</div>
  <p class="quote-text abs" style="left:775px;top:168px">It is a long established fact that a reader will be distracted by the readable content...</p>
</section>

<section class="types abs">
  <h2 class="section-title upper">Diamond Types</h2>
  <p class="types-text upper">At Lunacrest Gems we specialise in creating beautiful jewellery and diamond engagement rings using the very best diamonds, gemstones and precious metals from Australia and around the world.</p>
  <div class="type-card abs" style="left:172px">
    <div class="type-photo" role="img" aria-label="Gold ring set with diamonds" style="background:linear-gradient(135deg,#3a3530,#8a6a48 50%,#2a2622)"></div>
    <div class="type-name upper">Diamond Engagement Rings</div>
    <div class="type-link upper">[ Click here for view details ]</div>
  </div>
  <div class="type-card abs" style="left:391px">
    <div class="type-photo" role="img" aria-label="Silver diamond cluster ring" style="background:radial-gradient(circle at 50% 45%,#e0e0e0,#777 45%,#2a2a2a)"></div>
    <div class="type-name upper">Diamond Engagement Rings</div>
    <div class="type-link upper">[ Click here for view details ]</div>
  </div>
  <div class="type-card abs" style="left:611px">
    <div class="type-photo" role="img" aria-label="Pearl rings on dark background" style="background:linear-gradient(135deg,#1e1e1e,#4a4a50 50%,#151515)"></div>
    <div class="type-name upper">Diamond Engagement Rings</div>
    <div class="type-link upper">[ Click here for view details ]</div>
  </div>
  <div class="type-card abs" style="left:831px">
    <div class="type-photo" role="img" aria-label="Gold buckle ring with diamonds" style="background:linear-gradient(135deg,#3a3a3a,#8a6e4c 50%,#2e2e2e)"></div>
    <div class="type-name upper">Diamond Engagement Rings</div>
    <div class="type-link upper">[ Click here for view details ]</div>
  </div>
</section>

<footer class="site-footer abs">
  <span class="foot-link abs upper" style="left:175px">Home</span>
  <span class="foot-link abs upper" style="left:231px">About Us</span>
  <span class="foot-link abs upper" style="left:306px">Contact Us</span>
  <span class="foot-link abs upper" style="left:391px">Gallery</span>
  <span class="foot-link abs upper" style="left:458px">Testimonials</span>
  <span class="foot-link abs upper" style="left:551px">Diamond Types</span>
  <div class="copyright abs upper">© 2014. Lunacrest Gems. All rights reserved.</div>
  <span class="social abs" style="left:884px"></span>
  <span class="social abs" style="left:922px"></span>
  <span class="social abs" style="left:960px"></span>
  <span class="social abs" style="left:998px"></span>
</footer>

</body>
</html>
```